Landscape design build company door flyer

I would like this flyer to convey a high-level of professionalism for a company that is excellent with communication with their clients as well as a company that does incredible installations

Went on vacation/holiday

```html
<!DOCTYPE html>
<html lang="en">
<head>
<meta charset="utf-8">
<title>Cedarline Builders – Outdoor Living Flyer</title>
<link href="https://fonts.googleapis.com/css2?family=Montserrat:wght@400;500;600;700;800&display=swap" rel="stylesheet">
<style>
  :root{
    --navy:#1a3148;
    --navy-deep:#162a3e;
    --gold:#f8b311;
    --white:#ffffff;
    --flank:#f1f1f1;
    --page:#e7e7e7;
    --ink:#1a3148;
  }
  *{margin:0;padding:0;box-sizing:border-box}
  html,body{width:1200px;height:1029px;overflow:hidden;background:var(--page)}
  body{position:relative;font-family:'Montserrat',Arial,sans-serif}
  .flyer{
    position:absolute;left:211px;top:14px;
    width:1122px;height:1444px;
    transform:scale(0.6925);transform-origin:0 0;
    background:var(--white);overflow:hidden;
  }
  .hero{position:absolute;left:0;top:72px;width:1122px;height:943px;background:linear-gradient(160deg,var(--navy) 0%,var(--navy-deep) 100%)}
  .logo-frame{position:absolute;left:0;top:0}
  .brand{
    position:absolute;left:420px;top:0;width:270px;height:198px;
    display:flex;align-items:center;justify-content:center;
    font-weight:700;font-size:26px;color:var(--navy);letter-spacing:.5px;text-align:center;line-height:1.15;
  }
  .headline{
    position:absolute;left:0;top:244px;width:1122px;text-align:center;
    font-weight:800;font-size:66px;line-height:68px;color:var(--white);letter-spacing:.5px;
  }
  .headline .accent{color:var(--gold)}
  .about{position:absolute;left:87px;top:503px;width:390px;color:var(--white)}
  .section-title{font-weight:600;font-size:27px;letter-spacing:.3px}
  .about p{font-size:17.4px;line-height:21.45px;text-align:justify;font-weight:500;margin-top:12px;hyphens:auto}
  .about p + p{margin-top:21px}
  .photo{position:absolute}
  .p-deck{left:532px;top:513px;width:188px;height:187px;background:linear-gradient(180deg,#5d8a3c 0%,#8a4a2a 55%,#b05a30 100%)}
  .p-kitchen{left:736px;top:513px;width:300px;height:187px;background:linear-gradient(180deg,#b0784a 0%,#3c4a44 45%,#6d6c68 100%)}
  .p-pool{left:532px;top:716px;width:188px;height:130px;background:linear-gradient(180deg,#d9d5cc 0%,#8fb79a 50%,#4aa6a2 100%)}
  .p-steps{left:532px;top:860px;width:188px;height:131px;background:linear-gradient(180deg,#6e5a3e 0%,#6f7172 40%,#8c8d8c 100%)}
  .p-firepit{left:736px;top:716px;width:300px;height:276px;background:linear-gradient(180deg,#3f6fb3 0%,#2f5a94 40%,#3a2f2c 62%,#8a6a55 100%)}
  .services{position:absolute;left:87px;top:1030px;color:var(--ink)}
  .services .section-title{color:var(--ink)}
  .service{position:absolute;display:flex;align-items:center;gap:14px;font-weight:700;font-size:16.5px;color:var(--ink);white-space:nowrap}
  .service svg{width:38px;height:40px;flex:none}
  .seal{position:absolute;left:865px;top:1063px;width:170px;height:170px;border-radius:50%;
    background:radial-gradient(circle,#2a2f35 0 52%,#c9a12c 53% 100%);box-shadow:inset 0 0 0 6px #8a6d16}
  .contact{position:absolute;left:0;top:1265px;width:1122px;height:170px;background:var(--navy)}
  .contact-title{position:absolute;left:88px;top:22px;font-weight:600;font-size:24px;color:var(--white)}
  .phone-icon{position:absolute;left:85px;top:60px;width:56px;height:58px}
  .phone{position:absolute;left:160px;top:50px;font-weight:600;font-size:62px;color:var(--gold);letter-spacing:.5px}
  .email{position:absolute;right:42px;top:70px;font-weight:400;font-size:23px;color:var(--white);letter-spacing:.3px}
</style>
</head>
<body>
<main class="flyer">
  <section class="hero"></section>

  <svg class="logo-frame" width="1122" height="260" viewBox="0 0 1122 260" aria-hidden="true">
    <polygon points="330,0 780,0 780,72 690,198 420,198 330,72" fill="var(--flank)"/>
    <rect x="420" y="0" width="270" height="198" fill="var(--white)"/>
    <line x1="420" y1="198" x2="420" y2="246" stroke="#111" stroke-width="1.5"/>
    <line x1="690" y1="198" x2="690" y2="246" stroke="#111" stroke-width="1.5"/>
  </svg>
  <div class="brand">CEDARLINE<br>BUILDERS</div>

  <h1 class="headline">LET’S CREATE<br><span class="accent">YOUR DREAM OUTDOOR</span><br>LIVING SPACE!</h1>

  <section class="about">
    <h2 class="section-title">ABOUT US</h2>
    <p>Discover the endless possibilities for your outdoor space with The Cedarline Builders Team. Our team of skilled artisans is dedicated to turning your outdoor space into a breathtaking oasis that you’ll love coming home to. Whether it’s a cozy patio for intimate gatherings, a sprawling deck to host memorable parties, or a custom paver driveway that adds instant curb appeal, our high-quality craftsmanship ensures stunning results that exceed your expectations.</p>
    <p>From concept to completion, we take pride in every detail, using the finest materials to withstand Seattle’s climate while adding timeless elegance to your property. Embrace the Pacific Northwest lifestyle and create cherished moments with family and friends in a captivating outdoor haven.</p>
  </section>

  <div class="photo p-deck" role="img" aria-label="Wooden deck with patio chairs and a pergola among trees"></div>
  <div class="photo p-kitchen" role="img" aria-label="Covered outdoor kitchen with stone fireplace"></div>
  <div class="photo p-pool" role="img" aria-label="Backyard pool beside a modern house"></div>
  <div class="photo p-steps" role="img" aria-label="Stone retaining wall with steps"></div>
  <div class="photo p-firepit" role="img" aria-label="Lakeside paver patio with firepit and lounge chairs at dusk"></div>

  <section class="services">
    <h2 class="section-title">OUR SERVICES</h2>
  </section>

  <div class="service" style="left:88px;top:1091px"><svg viewBox="0 0 38 40" aria-hidden="true"><path d="M3 38V14L19 3l16 11v24" fill="none" stroke="var(--ink)" stroke-width="2.5"/><path d="M11 18h16l-2 4H13zM19 22v10M12 32h14M13 26h12" fill="none" stroke="var(--ink)" stroke-width="2"/></svg>Paver Patios</div>
  <div class="service" style="left:88px;top:1147px"><svg viewBox="0 0 38 40" aria-hidden="true"><path d="M3 38V14L19 3l16 11v24" fill="none" stroke="var(--ink)" stroke-width="2.5"/><path d="M7 32l6-9h12l6 9z" fill="var(--ink)"/></svg>Paver Driveways</div>
  <div class="service" style="left:88px;top:1208px"><svg viewBox="0 0 38 40" aria-hidden="true"><path d="M3 38V14L19 3l16 11v24" fill="none" stroke="var(--ink)" stroke-width="2.5"/><path d="M10 18h10v4H10zM14 23h10v4H14zM18 28h8v4h-8z" fill="var(--ink)"/></svg>Retaining Walls</div>

  <div class="service" style="left:328px;top:1091px"><svg viewBox="0 0 38 40" aria-hidden="true"><path d="M3 38V14L19 3l16 11v24" fill="none" stroke="var(--ink)" stroke-width="2.5"/><path d="M14 26V14h8M14 19h8M22 14v12M10 28q3 2 6 0t6 0t6 0M10 32q3 2 6 0t6 0t6 0" fill="none" stroke="var(--ink)" stroke-width="1.8"/></svg>Pools</div>
  <div class="service" style="left:328px;top:1147px"><svg viewBox="0 0 38 40" aria-hidden="true"><path d="M3 38V14L19 3l16 11v24" fill="none" stroke="var(--ink)" stroke-width="2.5"/><path d="M10 18h18M10 22h18v10H10zM14 22v10M19 22v10M24 22v10" fill="none" stroke="var(--ink)" stroke-width="1.8"/></svg>Decks &amp; Railings</div>
  <div class="service" style="left:328px;top:1208px"><svg viewBox="0 0 38 40" aria-hidden="true"><path d="M3 38V14L19 3l16 11v24" fill="none" stroke="var(--ink)" stroke-width="2.5"/><path d="M10 24l9-8 9 8v9H10z" fill="none" stroke="var(--ink)" stroke-width="2"/><rect x="16" y="26" width="6" height="7" fill="var(--ink)"/></svg>Firepits &amp; Fireplaces</div>

  <div class="service" style="left:575px;top:1091px"><svg viewBox="0 0 38 40" aria-hidden="true"><path d="M3 38V14L19 3l16 11v24" fill="none" stroke="var(--ink)" stroke-width="2.5"/><path d="M16 16h6v3l1 8h-8l1-8zM19 27v6M15 33h8" fill="none" stroke="var(--ink)" stroke-width="1.8"/></svg>Outdoor Lighting</div>
  <div class="service" style="left:575px;top:1147px"><svg viewBox="0 0 38 40" aria-hidden="true"><path d="M3 38V14L19 3l16 11v24" fill="none" stroke="var(--ink)" stroke-width="2.5"/><circle cx="19" cy="25" r="8" fill="none" stroke="var(--ink)" stroke-width="1.8"/><path d="M19 20v10M14 25h10" stroke="var(--ink)" stroke-width="1.8"/></svg>And More...</div>

  <div class="seal" role="img" aria-label="Experience seal"></div>

  <footer class="contact">
    <h2 class="contact-title">CONTACT US TODAY</h2>
    <svg class="phone-icon" viewBox="0 0 56 58" aria-hidden="true">
      <path d="M6 8l10-4 8 13-6 5q4 10 14 15l5-6 13 8-4 10q-4 5-12 2Q12 41 3 19q-2-7 3-11z" fill="var(--gold)"/>
      <path d="M32 14q9 2 11 11M32 6q15 3 18 19" fill="none" stroke="var(--gold)" stroke-width="4" stroke-linecap="round"/>
    </svg>
    <div class="phone">[206]-555-0148</div>
    <div class="email">info@cedarlinebuilders.com</div>
  </footer>
</main>
</body>
</html>
```